Digital Marketing Website Redesign, modern, fresh, dynamic

Hi there, we would like to freshen up our website and create a new dynamic look. We are a digital marketing agency who specialise in digital transformation in the form of creating websites for appointment bookings. Our clients are service businesses such as hairdressers, dentists and doctors who's patients need to book appointments with them.

Our company name is Tallomex with the point being we can help increase your revenue curve by increasing your appointment bookings.

Our services include building the website, creating campaigns to drive traffic, increasing conversions and monitoring and reporting.

We are playing with a tagline of 'Step into your Digital Transformation' as we have a 5 step journey that customers can take with us getting them from zero to full appointment bookings.

Our current website is www.tallomex-sample.com

You can see a draft design that I mocked up on Canva here https://www.draftboard-sample.com/design/QXB82LmpR7T/KpoW39dnFsYbZet_wqe_OPa/edit?utm_content=QXB82LmpR7T&utm_campaign=designshare&utm_medium=link2&utm_source=sharebutton

Also attached some other homepage ideas. In regard to photos we are open to ideas.

Please let if you need any more information to provide us with an initial design. Thanks million and I look forward to receiving fantastic designs :)

Marian Dobbs
Tallomex

Target Market(s)

Appointment based businesses such as hairdressers, dentists, doctors

Industry/Entity Type

Marketing and Digital

Coding

Coded - Design and coding required

Number of Pages Required

1 page

Colors
0094D4
00A9DD
6FCCEA
C7EBF8
E9F6FB

Requirements
Must have
• Appointment booking CTA
Nice to have
• A website we like https://www.fergalwhitty-sample.ie

```html
<!DOCTYPE html>
<html lang="en">
<head>
<meta charset="utf-8">
<title>Tallomex – Website Mobile View</title>
<link href="https://fonts.googleapis.com/css2?family=Poppins:ital,wght@0,400;0,500;0,600;0,700;1,400&display=swap" rel="stylesheet">
<style>
:root{
  --navy:#03182a;
  --navy-input:#13293b;
  --blue:#0094D4;
  --blue-bright:#00A9DD;
  --blue-soft:#6FCCEA;
  --ink:#0b1b2a;
  --muted:#4a5560;
  --star:#F5B400;
  --white:#ffffff;
}
*{margin:0;padding:0;box-sizing:border-box}
html,body{width:1200px;height:1200px;overflow:hidden;background:#fff}
body{position:relative;font-family:'Poppins',sans-serif;color:var(--ink)}
.abs{position:absolute}

/* intro */
.brand-title{left:48px;top:118px;font-size:39px;font-weight:700;color:var(--navy);letter-spacing:-.3px}
.brand-sub{left:48px;top:195px;font-size:24px;font-weight:500;color:#0a72bb;line-height:35px}
.dark-block{left:0;top:781px;width:292px;height:419px;background:var(--navy);border-top-right-radius:56px}
.award-badge{left:121px;top:728px;width:108px;height:108px;background:#0a72bb;border-radius:26px;display:flex;align-items:center;justify-content:center}

/* screen frames */
.frame{background:#fff;box-shadow:0 0 40px rgba(0,20,40,.06)}
.frame-footer{left:324px;top:0;width:263px;height:289px;border-radius:0 0 28px 28px}
.frame-home{left:324px;top:314px;width:263px;height:886px;border-radius:28px 28px 0 0}
.frame-reviews{left:612px;top:0;width:264px;height:1200px}
.frame-team{left:900px;top:0;width:263px;height:1200px}

/* footer screen */
.footer-panel{left:336px;top:0;width:240px;height:276px;background:var(--navy);border-radius:0 0 28px 28px;color:#fff}
.footer-panel h4{position:absolute;left:11px;top:12px;font-size:11px;font-weight:600}
.hours-row{position:absolute;left:11px;width:218px;display:flex;justify-content:space-between;font-size:9.3px}
.email-field{position:absolute;left:11px;top:122px;width:218px;height:35px;background:var(--navy-input);border-radius:6px;font-size:9.3px;color:#aab4bd;padding:12px 0 0 17px}
.subscribe-btn{position:absolute;left:11px;top:169px;width:218px;height:31px;background:var(--blue);border-radius:16px;font-size:9.3px;font-weight:600;text-align:center;line-height:31px}
.copyright{position:absolute;left:0;width:240px;top:246px;text-align:center;font-size:9.3px;color:#d8dee4}
.copyright b{font-weight:600;color:#fff}

/* home screen */
.logo-word{left:347px;top:342px;font-size:16px;font-weight:600;color:#1d4f9c}
.logo-dot{left:405px;top:337px;width:6px;height:6px;border-radius:50%;background:#9cc92a}
.menu-btn{left:521px;top:340px;width:27px;height:27px;border-radius:50%;background:var(--blue);display:flex;align-items:center;justify-content:center}
.hero{left:336px;top:381px;width:240px;height:446px;background:linear-gradient(180deg,#1e5a82 0%,#103a5a 40%,#0a2236 75%,#05121d 100%)}
.hero h1{position:absolute;left:11px;top:188px;width:225px;font-size:20.5px;font-weight:600;line-height:30px;color:#fff}
.hero p{position:absolute;left:11px;top:257px;width:222px;font-size:9.3px;line-height:15.6px;color:#e2e9ef}
.pill{position:absolute;background:var(--blue);color:#fff;font-size:9.3px;font-weight:600;text-align:center;border-radius:16px}
.hero .pill{left:11px;top:359px;width:82px;height:31px;line-height:31px}
.dots{position:absolute;left:98px;top:414px;display:flex;gap:11px;align-items:center}
.dots span{width:5px;height:5px;border-radius:50%;background:#3b4a56}
.dots .on{width:10px;height:10px;border:1.5px solid #fff;background:var(--blue)}
.stat{left:336px;width:240px;text-align:center}
.stat-icon{width:17px;height:15px;margin:0 auto;background:var(--blue);border-radius:4px}
.stat-num{font-size:32px;font-weight:600;color:var(--navy);line-height:40px;margin-top:6px}
.stat-label{font-size:9.3px;color:#2c3742}

/* reviews */
.section-title{font-size:19px;font-weight:600;color:var(--navy);text-align:center}
.review-card{left:635px;width:217px;height:172px;background:#fff;border-radius:12px;box-shadow:0 4px 22px rgba(0,20,40,.07);padding:16px 0 0 17px}
.stars{display:flex;gap:4px}
.review-card p{margin-top:10px;font-size:9.3px;font-style:italic;line-height:15.6px;color:#3b4650;width:195px}
.review-card .author{margin-top:10px;font-size:9px;font-weight:600;color:var(--blue)}
.nav-arrow{top:655px;width:27px;height:27px;border-radius:50%;background:var(--blue);display:flex;align-items:center;justify-content:center}
.service-card{left:624px;width:239px;color:#fff;text-align:center}
.service-card h3{position:absolute;left:0;width:239px;font-size:18.5px;font-weight:600}
.service-card p{position:absolute;left:12px;width:215px;font-size:9.3px;line-height:15.6px;color:#e6ebef}
.service-card .pill{left:84px;width:71px;height:31px;line-height:31px}

/* team */
.team-intro{left:912px;top:48px;width:239px;text-align:center;font-size:9.3px;line-height:15.6px;color:#2c3742}
.member{left:912px;width:239px;height:234px;color:#fff;text-align:center}
.member .name{position:absolute;left:0;width:239px;top:181px;font-size:14px;font-weight:600}
.member .role{position:absolute;left:0;width:239px;top:202px;font-size:9.3px}
.cta-band{left:912px;top:1090px;width:239px;height:110px;background:linear-gradient(160deg,#2aa6dc,#0a86c6)}
.cta-band h2{position:absolute;left:11px;top:46px;font-size:19px;font-weight:600;line-height:27px;color:#fff}
</style>
</head>
<body>

<!-- intro -->
<div class="abs brand-title">Tallomex</div>
<div class="abs brand-sub">Website Mobile<br>View</div>
<div class="abs dark-block"></div>
<div class="abs award-badge">
  <svg width="58" height="58" viewBox="0 0 58 58" fill="none" stroke="#fff" stroke-width="3.2" stroke-linejoin="round" stroke-linecap="round">
    <circle cx="29" cy="22" r="15"/>
    <circle cx="29" cy="22" r="10"/>
    <polygon points="29,16 30.8,20 35,20.3 31.8,23 32.8,27.2 29,25 25.2,27.2 26.2,23 23,20.3 27.2,20"/>
    <path d="M18 33 L10 45 L17 45 L20 52 L26 38"/>
    <path d="M40 33 L48 45 L41 45 L38 52 L32 38"/>
  </svg>
</div>

<!-- footer screen -->
<div class="abs frame frame-footer"></div>
<div class="abs footer-panel">
  <h4>Opening Hours</h4>
  <div class="hours-row" style="top:53px"><span>Monday - Friday</span><span>8.30am - 6.30pm</span></div>
  <div class="hours-row" style="top:80px"><span>Saturday and Sunday</span><span>Closed</span></div>
  <div class="email-field">Email Address</div>
  <div class="subscribe-btn">Subscribe Now</div>
  <div class="copyright">Copyright © 2024 <b>Tallomex</b> · All Rights Reserved</div>
</div>

<!-- home screen -->
<div class="abs frame frame-home"></div>
<div class="abs logo-word">Tallomex</div>
<div class="abs menu-btn">
  <svg width="11" height="8" viewBox="0 0 11 8" stroke="#fff" stroke-width="1.3"><line x1="0" y1="1" x2="11" y2="1"/><line x1="0" y1="4" x2="11" y2="4"/><line x1="0" y1="7" x2="11" y2="7"/></svg>
</div>
<div class="abs hero" role="img" aria-label="Person walking into a glowing blue digital tunnel">
  <h1>Step into your Digital Transformation</h1>
  <p>Digital transformation is a journey. At Tallomex we divide the journey into five key steps that take your business from comprehensive market research to full appointment bookings. Ready to go on that journey?</p>
  <div class="pill">Start Here</div>
  <div class="dots"><span class="on"></span><span></span><span></span></div>
</div>

<div class="abs stat" style="top:874px">
  <div class="stat-icon"></div>
  <div class="stat-num">762</div>
  <div class="stat-label">Appointments Booked</div>
</div>
<div class="abs stat" style="top:979px">
  <div class="stat-icon"></div>
  <div class="stat-num">31</div>
  <div class="stat-label">Marketing Campaigns</div>
</div>
<div class="abs stat" style="top:1084px">
  <div class="stat-icon"></div>
  <div class="stat-num">25%</div>
  <div class="stat-label">Website Traffic Increase</div>
</div>
<div class="abs stat" style="top:1188px"><div class="stat-icon"></div></div>

<!-- reviews screen -->
<div class="abs frame frame-reviews"></div>
<div class="abs section-title" style="left:612px;width:264px;top:18px">Why others choose us?</div>

<div class="abs review-card" style="top:75px">
  <div class="stars">
    <svg width="9" height="9" viewBox="0 0 10 10"><polygon fill="#F5B400" points="5,0 6.3,3.4 10,3.6 7.1,5.9 8.1,9.5 5,7.5 1.9,9.5 2.9,5.9 0,3.6 3.7,3.4"/></svg>
    <svg width="9" height="9" viewBox="0 0 10 10"><polygon fill="#F5B400" points="5,0 6.3,3.4 10,3.6 7.1,5.9 8.1,9.5 5,7.5 1.9,9.5 2.9,5.9 0,3.6 3.7,3.4"/></svg>
    <svg width="9" height="9" viewBox="0 0 10 10"><polygon fill="#F5B400" points="5,0 6.3,3.4 10,3.6 7.1,5.9 8.1,9.5 5,7.5 1.9,9.5 2.9,5.9 0,3.6 3.7,3.4"/></svg>
    <svg width="9" height="9" viewBox="0 0 10 10"><polygon fill="#F5B400" points="5,0 6.3,3.4 10,3.6 7.1,5.9 8.1,9.5 5,7.5 1.9,9.5 2.9,5.9 0,3.6 3.7,3.4"/></svg>
    <svg width="9" height="9" viewBox="0 0 10 10"><polygon fill="#F5B400" points="5,0 6.3,3.4 10,3.6 7.1,5.9 8.1,9.5 5,7.5 1.9,9.5 2.9,5.9 0,3.6 3.7,3.4"/></svg>
  </div>
  <p>Having had to close for Covid-19 in March 2020, Tallomex’s Online Booking System really helped us as within a few days of the Swiss announcement that we could re-open in May we received over 100 appointment reservations..</p>
  <div class="author">Helena Roth, Owner, Salon Brera Zug</div>
</div>

<div class="abs review-card" style="top:265px">
  <div class="stars">
    <svg width="9" height="9" viewBox="0 0 10 10"><polygon fill="#F5B400" points="5,0 6.3,3.4 10,3.6 7.1,5.9 8.1,9.5 5,7.5 1.9,9.5 2.9,5.9 0,3.6 3.7,3.4"/></svg>
    <svg width="9" height="9" viewBox="0 0 10 10"><polygon fill="#F5B400" points="5,0 6.3,3.4 10,3.6 7.1,5.9 8.1,9.5 5,7.5 1.9,9.5 2.9,5.9 0,3.6 3.7,3.4"/></svg>
    <svg width="9" height="9" viewBox="0 0 10 10"><polygon fill="#F5B400" points="5,0 6.3,3.4 10,3.6 7.1,5.9 8.1,9.5 5,7.5 1.9,9.5 2.9,5.9 0,3.6 3.7,3.4"/></svg>
    <svg width="9" height="9" viewBox="0 0 10 10"><polygon fill="#F5B400" points="5,0 6.3,3.4 10,3.6 7.1,5.9 8.1,9.5 5,7.5 1.9,9.5 2.9,5.9 0,3.6 3.7,3.4"/></svg>
    <svg width="9" height="9" viewBox="0 0 10 10"><polygon fill="#F5B400" points="5,0 6.3,3.4 10,3.6 7.1,5.9 8.1,9.5 5,7.5 1.9,9.5 2.9,5.9 0,3.6 3.7,3.4"/></svg>
  </div>
  <p>Having had to close for Covid-19 in March 2020, Tallomex’s Online Booking System really helped us as within a few days of the Swiss announcement that we could re-open in May we received over 100 appointment reservations..</p>
  <div class="author">Helena Roth, Owner, Salon Brera Zug</div>
</div>

<div class="abs review-card" style="top:454px">
  <div class="stars">
    <svg width="9" height="9" viewBox="0 0 10 10"><polygon fill="#F5B400" points="5,0 6.3,3.4 10,3.6 7.1,5.9 8.1,9.5 5,7.5 1.9,9.5 2.9,5.9 0,3.6 3.7,3.4"/></svg>
    <svg width="9" height="9" viewBox="0 0 10 10"><polygon fill="#F5B400" points="5,0 6.3,3.4 10,3.6 7.1,5.9 8.1,9.5 5,7.5 1.9,9.5 2.9,5.9 0,3.6 3.7,3.4"/></svg>
    <svg width="9" height="9" viewBox="0 0 10 10"><polygon fill="#F5B400" points="5,0 6.3,3.4 10,3.6 7.1,5.9 8.1,9.5 5,7.5 1.9,9.5 2.9,5.9 0,3.6 3.7,3.4"/></svg>
    <svg width="9" height="9" viewBox="0 0 10 10"><polygon fill="#F5B400" points="5,0 6.3,3.4 10,3.6 7.1,5.9 8.1,9.5 5,7.5 1.9,9.5 2.9,5.9 0,3.6 3.7,3.4"/></svg>
    <svg width="9" height="9" viewBox="0 0 10 10"><polygon fill="#F5B400" points="5,0 6.3,3.4 10,3.6 7.1,5.9 8.1,9.5 5,7.5 1.9,9.5 2.9,5.9 0,3.6 3.7,3.4"/></svg>
  </div>
  <p>Having had to close for Covid-19 in March 2020, Tallomex’s Online Booking System really helped us as within a few days of the Swiss announcement that we could re-open in May we received over 100 appointment reservations..</p>
  <div class="author">Helena Roth, Owner, Salon Brera Zug</div>
</div>

<div class="abs nav-arrow" style="left:711px">
  <svg width="12" height="10" viewBox="0 0 12 10" fill="none" stroke="#fff" stroke-width="1.4" stroke-linecap="round" stroke-linejoin="round"><line x1="1" y1="5" x2="11" y2="5"/><polyline points="5,1 1,5 5,9"/></svg>
</div>
<div class="abs nav-arrow" style="left:749px">
  <svg width="12" height="10" viewBox="0 0 12 10" fill="none" stroke="#fff" stroke-width="1.4" stroke-linecap="round" stroke-linejoin="round"><line x1="1" y1="5" x2="11" y2="5"/><polyline points="7,1 11,5 7,9"/></svg>
</div>

<div class="abs service-card" style="top:725px;height:254px;background:linear-gradient(180deg,#8a97a3 0%,#5b6873 45%,#2b333b 100%)" role="img" aria-label="Team sketching campaign wireframes on a desk">
  <h3 style="top:62px">Creative Campaigns</h3>
  <p style="top:98px">Digital transformation is a journey. At Tallomex we divide the journey into five key steps that take your business from comprehensive.</p>
  <div class="pill" style="top:163px">Sign Up</div>
</div>
<div class="abs service-card" style="top:979px;height:221px;background:linear-gradient(180deg,#56606a 0%,#6c7882 50%,#3c454d 100%)" role="img" aria-label="Hands reviewing research charts on paper">
  <h3 style="top:62px">Market Research</h3>
  <p style="top:98px">Digital transformation is a journey. At Tallomex we divide the journey into five key steps that take your business from comprehensive.</p>
  <div class="pill" style="top:162px">Sign Up</div>
</div>

<!-- team screen -->
<div class="abs frame frame-team"></div>
<div class="abs section-title" style="left:900px;width:263px;top:9px">Our Team</div>
<div class="abs team-intro">From business management and web development to creative campaign delivery and social media expertise, our team has all the experience your business needs to it to the top of its digital game.</div>

<div class="abs member" style="top:153px;height:235px;background:linear-gradient(180deg,#7d8a6a 0%,#6b7266 45%,#3a4048 80%,#1c2228 100%)" role="img" aria-label="Portrait of account manager Ronan">
  <div class="name">Ronan</div><div class="role">Account Manager</div>
</div>
<div class="abs member" style="top:388px;background:linear-gradient(180deg,#a9b0b6 0%,#8a8f93 45%,#454a50 80%,#1e2328 100%)" role="img" aria-label="Portrait of account manager Maeve">
  <div class="name">Maeve</div><div class="role">Account Manager</div>
</div>
<div class="abs member" style="top:622px;background:linear-gradient(180deg,#c9cccd 0%,#9c9a98 45%,#3c3f44 80%,#1b1f24 100%)" role="img" aria-label="Portrait of account manager Lucia">
  <div class="name">Lucia</div><div class="role">Account Manager</div>
</div>
<div class="abs member" style="top:856px;background:linear-gradient(160deg,#e2872a 0%,#b9703a 35%,#5d4a3e 70%,#1e2328 100%)" role="img" aria-label="Portrait of account manager Priya">
  <div class="name">Priya</div><div class="role">Account Manager</div>
</div>
<div class="abs cta-band" role="img" aria-label="Office wall with sticky notes in blue tint">
  <h2>Start your Digital<br>Transformation</h2>
</div>

</body>
</html>
```